Business Card Design

We need a business card designed for our new company. Prefer a black card with white logo & writing.

Contact Information for Business Card

Ted Galloway, address: 7-4812 Fernhollow Road, Cedarvale, BC, V3K 8R2, Office Phone: 604-712-3390, Cell: 604-947-2164, Email: ted@resinworkshub.ca

Colors

Designer to choose only greyscale colors for use in the design.

```html
<!DOCTYPE html>
<html lang="en">
<head>
<meta charset="utf-8">
<title>Resinworks Hub – Business Card</title>
<link rel="stylesheet" href="https://fonts.googleapis.com/css2?family=Poppins:wght@300;400;700&display=swap">
<style>
  :root {
    --backdrop: #202022;
    --card: #27272a;
    --ink: #ffffff;
    --ink-soft: #e6e6e6;
  }
  * { margin: 0; padding: 0; box-sizing: border-box; }
  html, body { width: 1200px; height: 711px; overflow: hidden; }
  body {
    background: var(--backdrop);
    font-family: "Poppins", sans-serif;
    color: var(--ink);
    position: relative;
  }
  .card {
    position: absolute;
    top: 62px;
    width: 340px;
    height: 588px;
    background: var(--card);
    border-radius: 22px;
    box-shadow: 0 14px 30px rgba(0,0,0,.55);
    overflow: hidden;
  }
  .card-front { left: 215px; }
  .card-back { left: 645px; }

  /* Front */
  .front-brand {
    position: absolute;
    left: 50%;
    top: 50%;
    transform: translate(-50%, -50%) rotate(-90deg);
    display: flex;
    align-items: center;
    gap: 14px;
    white-space: nowrap;
  }
  .brand-mark {
    width: 22px; height: 22px;
    background: var(--ink);
    border-radius: 50%;
  }
  .front-brand .brand-name {
    font-weight: 700;
    font-size: 40px;
    letter-spacing: 1px;
  }

  /* Back */
  .back-brand {
    position: absolute;
    top: 92px;
    left: 0; right: 0;
    display: flex;
    justify-content: center;
    align-items: center;
    gap: 10px;
  }
  .back-brand .brand-mark { width: 14px; height: 14px; }
  .back-brand .brand-name { font-weight: 700; font-size: 24px; letter-spacing: .5px; }

  .dot-row { position: absolute; left: 0; width: 340px; height: 20px; }
  .dot-row circle { fill: var(--ink); }

  .person {
    position: absolute;
    top: 268px;
    left: 0; right: 0;
    text-align: center;
  }
  .person-name { font-size: 31px; font-weight: 300; line-height: 1.1; }
  .person-name strong { font-weight: 700; }
  .person-title { font-size: 14px; font-weight: 300; color: var(--ink-soft); }

  .contact-icons { position: absolute; top: 346px; left: 0; width: 340px; height: 28px; }
  .contact-icons circle.badge { fill: var(--ink); }
  .contact-icons .glyph { fill: none; stroke: var(--card); stroke-width: 1.6; stroke-linecap: round; stroke-linejoin: round; }

  .contact-list {
    position: absolute;
    top: 384px;
    left: 0; right: 0;
    list-style: none;
    text-align: center;
    font-size: 14px;
    font-weight: 300;
    line-height: 19px;
  }

  .address-pin { position: absolute; top: 496px; left: 0; width: 340px; height: 28px; }
  .address-pin circle.badge { fill: var(--ink); }
  .address-pin .glyph { fill: none; stroke: var(--card); stroke-width: 1.6; }

  .address {
    position: absolute;
    top: 530px;
    left: 0; right: 0;
    text-align: center;
    font-style: normal;
    font-size: 14px;
    font-weight: 300;
    line-height: 19px;
  }
</style>
</head>
<body>

<section class="card card-front">
  <div class="front-brand">
    <span class="brand-mark"></span>
    <span class="brand-name">RESINWORKS HUB</span>
  </div>
</section>

<section class="card card-back">
  <div class="back-brand">
    <span class="brand-mark"></span>
    <span class="brand-name">RESINWORKS HUB</span>
  </div>

  <svg class="dot-row" style="top:246px" viewBox="0 0 340 20" aria-hidden="true">
    <circle cx="160" cy="10" r="1.5"/><circle cx="180" cy="10" r="2"/><circle cx="200" cy="10" r="2.5"/>
    <circle cx="222" cy="10" r="3"/><circle cx="245" cy="10" r="3.5"/><circle cx="270" cy="10" r="4"/>
    <circle cx="297" cy="10" r="4.5"/><circle cx="326" cy="10" r="5"/>
  </svg>

  <div class="person">
    <p class="person-name"><strong>Ted</strong> Galloway</p>
    <p class="person-title">Founder &amp; CEO</p>
  </div>

  <svg class="contact-icons" viewBox="0 0 340 28" aria-hidden="true">
    <circle class="badge" cx="14" cy="14" r="5"/><circle class="badge" cx="36" cy="14" r="6"/><circle class="badge" cx="60" cy="14" r="7"/>
    <circle class="badge" cx="104" cy="14" r="13"/>
    <path class="glyph" d="M98 9c0 6 5 11 11 11l2-3-3-2-2 1c-2-1-4-3-5-5l1-2-2-3z"/>
    <circle class="badge" cx="138" cy="14" r="13"/>
    <path class="glyph" d="M133 12h10v7h-10zM135 12v-4h6v4M135 16h6"/>
    <circle class="badge" cx="172" cy="14" r="13"/>
    <path class="glyph" d="M165 9h14v10h-14zM165 9l7 6 7-6"/>
    <circle class="badge" cx="206" cy="14" r="13"/>
    <circle class="glyph" cx="206" cy="14" r="7"/>
    <path class="glyph" d="M199 14h14M206 7c-3 4-3 10 0 14M206 7c3 4 3 10 0 14"/>
    <circle class="badge" cx="246" cy="14" r="7"/><circle class="badge" cx="270" cy="14" r="6"/><circle class="badge" cx="292" cy="14" r="5"/>
    <circle class="badge" cx="312" cy="14" r="4"/><circle class="badge" cx="330" cy="14" r="3"/>
  </svg>

  <ul class="contact-list">
    <li>604-712-3390</li>
    <li>604-947-2164</li>
    <li>www.resinworkshub.ca</li>
    <li>ted@resinworkshub.ca</li>
  </ul>

  <svg class="dot-row" style="top:468px" viewBox="0 0 340 20" aria-hidden="true">
    <circle cx="8" cy="10" r="1.5"/><circle cx="26" cy="10" r="2"/><circle cx="46" cy="10" r="2.5"/>
    <circle cx="68" cy="10" r="3"/><circle cx="92" cy="10" r="3.5"/><circle cx="118" cy="10" r="4"/>
    <circle cx="222" cy="10" r="4"/><circle cx="248" cy="10" r="3.5"/><circle cx="272" cy="10" r="3"/>
    <circle cx="294" cy="10" r="2.5"/><circle cx="314" cy="10" r="2"/><circle cx="332" cy="10" r="1.5"/>
  </svg>

  <svg class="address-pin" viewBox="0 0 340 28" aria-hidden="true">
    <circle class="badge" cx="82" cy="14" r="4"/><circle class="badge" cx="100" cy="14" r="5"/><circle class="badge" cx="120" cy="14" r="6"/><circle class="badge" cx="143" cy="14" r="7"/>
    <circle class="badge" cx="170" cy="14" r="13"/>
    <path class="glyph" d="M170 22c-4-5-6-8-6-11a6 6 0 0 1 12 0c0 3-2 6-6 11z"/>
    <circle class="glyph" cx="170" cy="11" r="2"/>
    <circle class="badge" cx="197" cy="14" r="7"/><circle class="badge" cx="220" cy="14" r="6"/><circle class="badge" cx="240" cy="14" r="5"/><circle class="badge" cx="258" cy="14" r="4"/>
  </svg>

  <address class="address">
    7-4812 Fernhollow Road,<br>
    Cedarvale, BC, V3K 8R2.
  </address>
</section>

</body>
</html>
```